Financial Services Flyer for Healthcare Providers

We need a flyer design for a product of Quorvel Financial (www.quorvelfinancial.example) called the PLAX program. Attached you will find the content for the flyer. Please use your own creativity and keep in mind the this is a product of Quorvel Financial, a financial services company that works in the field of healthcare. If you have any questions or comments, please feel free to ask....

Target Market(s)

Our target audience is healthcare providers.

Industry/Entity Type

Financial

Requirements
Must have
• Eye catching graphics and colors but still look fairly conservative since our audience is somewhat conservative.
Nice to have
• Nice looking, smiling, upbeat people in pictorial portions of the flyer.
Should not have
• Our clients are all found in America, so the look, feel and subtext should all target an American audience and not have the look and feel of being from outside of the US.

```html
<!DOCTYPE html>
<html lang="en">
<head>
<meta charset="utf-8">
<title>PLAX Program Flyer – Quorvel Financial</title>
<link rel="stylesheet" href="https://fonts.googleapis.com/css2?family=Open+Sans:wght@400;600;700&display=swap">
<style>
  :root {
    --page-bg: #ecebe8;
    --paper: #ffffff;
    --ink: #333333;
    --ink-soft: #444444;
    --accent: #16a6d6;
    --band-blue: #17a4d2;
    --panel-dark: #2f3032;
    --panel-text: #e6e6e6;
    --strip-gray: #55585b;
    --rule-gray: #b9babc;
    --photo-top: #e4e7ea;
    --photo-mid: #9fb2c8;
    --photo-low: #d9dde2;
  }
  * { margin: 0; padding: 0; box-sizing: border-box; }
  html, body {
    width: 1000px; height: 1200px; overflow: hidden;
    background: var(--page-bg);
    font-family: "Open Sans", Arial, sans-serif;
  }
  .flyer {
    position: absolute; left: 90px; top: 20px;
    width: 820px; height: 1160px;
    background: var(--paper);
    box-shadow: 0 4px 18px rgba(0,0,0,.18);
    overflow: hidden;
  }
  .hero-photo {
    position: absolute; left: 0; top: 0; width: 820px; height: 460px;
    background:
      radial-gradient(ellipse at 50% 75%, var(--photo-mid) 0%, rgba(159,178,200,0) 60%),
      linear-gradient(180deg, var(--photo-top) 0%, var(--photo-low) 100%);
  }
  .hero-band {
    position: absolute; left: 100px; top: 178px; width: 640px; height: 100px;
    background: rgba(150,170,195,.45);
  }
  .hero-title {
    position: absolute; left: 0; top: 186px; width: 820px; text-align: center;
    color: #fff; font-weight: 700; font-size: 46px; line-height: 1.1;
  }
  .hero-tagline {
    position: absolute; left: 0; top: 240px; width: 820px; text-align: center;
    color: #fff; font-size: 21px;
  }
  .divider-strip {
    position: absolute; left: 0; top: 460px; width: 820px; height: 20px;
    background: var(--strip-gray);
  }
  .intro { position: absolute; left: 33px; top: 506px; width: 760px; }
  .intro h2 {
    font-size: 29px; font-weight: 700; color: var(--ink); line-height: 1.2;
  }
  .intro h2 span { color: var(--accent); }
  .intro p {
    margin-top: 10px; font-size: 17px; line-height: 1.36; color: var(--ink-soft);
  }
  .intro-rule {
    position: absolute; left: 30px; top: 669px; width: 770px; height: 2px;
    background: linear-gradient(90deg, rgba(0,0,0,0), var(--rule-gray) 20%, var(--rule-gray) 80%, rgba(0,0,0,0));
  }
  .panel {
    position: absolute; top: 694px; height: 339px;
    background: var(--panel-dark);
    box-shadow: 4px 4px 8px rgba(0,0,0,.35);
    color: var(--panel-text);
  }
  .how-it-works { left: 0; width: 626px; padding: 32px 40px 0 35px; }
  .how-it-works h3 { font-size: 28px; font-weight: 700; color: #fff; margin-bottom: 14px; }
  .how-it-works h3 span { color: var(--accent); }
  .how-it-works p { font-size: 14.6px; line-height: 1.37; }
  .contact { left: 646px; width: 174px; padding: 14px 22px 0 0; text-align: right; }
  .contact h3 { font-size: 21px; font-weight: 700; color: #fff; margin-bottom: 14px; text-align: center; padding-left: 20px; }
  .contact h3 span { color: var(--accent); }
  .contact dt { font-size: 15px; font-weight: 700; color: var(--accent); line-height: 1.3; }
  .contact dd { font-size: 15px; line-height: 1.3; color: #fff; }
  .costs {
    position: absolute; left: 0; top: 1045px; width: 820px; height: 98px;
    background: var(--band-blue); color: #fff; padding: 10px 33px;
  }
  .costs h3 { font-size: 27px; font-weight: 700; line-height: 1.2; }
  .costs p { font-size: 13px; line-height: 1.35; margin-top: 4px; }
  .costs strong { font-weight: 700; }
  .bottom-rule {
    position: absolute; left: 0; top: 1146px; width: 820px; height: 7px;
    background: #a9abad;
  }
</style>
</head>
<body>
  <article class="flyer">
    <header>
      <div class="hero-photo" role="img" aria-label="Photo of five smiling healthcare professionals in white coats and scrubs with stethoscopes"></div>
      <div class="hero-band"></div>
      <h1 class="hero-title">PLAX Program</h1>
      <p class="hero-tagline">Get Plax Now !</p>
    </header>
    <div class="divider-strip"></div>

    <section class="intro">
      <h2>Underpaid Claims &amp; <span>Revenue Recovery</span></h2>
      <p>At Quorvel Financial, PLAX locates underpaid claims and turns write offs into added revenue. PLAX uses a genius revenue cycle application that identifies potentially underpaid claims for hospitals. Once revenue has been located, our medical billers correct the claims and appeal to insurance for payment.</p>
    </section>
    <div class="intro-rule"></div>

    <section class="panel how-it-works">
      <h3>How <span>PLAX</span> works ?</h3>
      <p>Remote Evaluation: With a secure and temporary login into any healthcare operating system a random account evaluation is conducted by a highly skilled revenue cycle auditor.<br>
      Data Exchange: When missed revenue is found, a simple data exchange will be recommended. Through the exchange, PLAX will arrange to connect your claims data into the PLAX work flow.<br>
      Collections: PLAX disperses underpaid claims to our medical billers for prompt recovery.</p>
    </section>

    <aside class="panel contact">
      <h3>Contact <span>Us</span></h3>
      <dl>
        <dt>Phone</dt><dd>000-000-000</dd>
        <dt>Fax</dt><dd>000-000-000</dd>
        <dt>Email</dt><dd>Youremailhere</dd>
        <dt>Address</dt><dd>Your Address here</dd>
      </dl>
    </aside>

    <section class="costs">
      <h3>Costs</h3>
      <p>PLAX charges nothing unless it finds and collects lost revenue for you!<br><strong>GET PLAX TODAY!</strong></p>
    </section>
    <div class="bottom-rule"></div>
  </article>
</body>
</html>
```